Business Card Design

Business Card for professional consulting firm working with large financial institutions.

Target Market(s)

Executive buyers

Industry/Entity Type

Banking

Contact Information for Business Card

Mild creativity wanted. Not boring, but do elaborate artwork.

Font styles to use
Serif
Sans Serif

Colors

Designer to choose colors to be used in the design.

Requirements
Must have
• Standard business card features - company name, individual name, telephone, website, email, locations.
Nice to have
• Two colors
Should not have
• too many colors, fancy printing, cartoons.

```html
<!DOCTYPE html>
<html lang="en">
<head>
<meta charset="utf-8">
<title>Northvale Business Card</title>
<link rel="stylesheet" href="https://fonts.googleapis.com/css2?family=Merriweather:wght@400&family=Roboto:wght@400;500&family=Roboto+Condensed:wght@500&display=swap">
<style>
  :root {
    --backdrop: #ebe7e1;
    --card-light: #f3f3f3;
    --card-dark: #1b1d1f;
    --ink: #2e2e2e;
    --ink-soft: #4a4a4a;
    --muted: #a9a9a9;
    --rule: #9a9a9a;
    --band: #c3c3c3;
    --white: #ffffff;
  }
  * { margin: 0; padding: 0; box-sizing: border-box; }
  html, body { width: 1200px; height: 960px; overflow: hidden; }
  body { background: var(--backdrop); position: relative; font-family: "Roboto", sans-serif; }

  .card { position: absolute; width: 600px; height: 342px; box-shadow: 0 2px 6px rgba(0,0,0,0.25); }
  .card--front { left: 314px; top: 113px; background: var(--card-light); }
  .card--back { left: 312px; top: 472px; background: var(--card-dark); }

  .wordmark { position: absolute; font-family: "Merriweather", serif; font-weight: 400; white-space: nowrap; }
  .card--front .wordmark { left: 78px; top: 56px; font-size: 27px; color: var(--ink); }
  .card--back .wordmark { left: 0; width: 600px; text-align: center; top: 142px; font-size: 35px; color: var(--white); }

  .person { position: absolute; right: 32px; top: 194px; text-align: right; }
  .person__name { font-family: "Roboto Condensed", sans-serif; font-weight: 500; font-size: 23px; color: var(--ink); line-height: 1; }
  .person__title { font-size: 14px; color: var(--muted); margin-top: 4px; }
  .accent-tab { position: absolute; right: 0; top: 192px; width: 10px; height: 46px; background: var(--band); }

  .rule { position: absolute; left: 34px; right: 35px; top: 249px; height: 1px; background: var(--rule); }

  .contacts { position: absolute; left: 34px; top: 262px; list-style: none; }
  .contacts li { display: flex; align-items: center; height: 19px; font-size: 14px; color: var(--ink-soft); }
  .contacts svg { width: 12px; height: 12px; margin-right: 8px; fill: var(--ink); }

  .address { position: absolute; right: 32px; top: 262px; text-align: right; font-size: 14px; line-height: 19px; color: var(--ink-soft); font-style: normal; }

  .web-band { position: absolute; left: 0; right: 0; top: 275px; height: 29px; background: var(--band); display: flex; align-items: center; justify-content: center; }
  .web-band span { color: var(--white); font-size: 14px; letter-spacing: 6.5px; }
</style>
</head>
<body>
  <section class="card card--front">
    <div class="wordmark">northvale</div>
    <div class="person">
      <div class="person__name">DANIEL REYES</div>
      <div class="person__title">CEO/FOUNDER</div>
    </div>
    <div class="accent-tab"></div>
    <div class="rule"></div>
    <ul class="contacts">
      <li><svg viewBox="0 0 12 12"><path d="M2.4 0.5l2 2.2-1 1.4c0.8 1.7 2 2.9 3.6 3.6l1.4-1 2.2 2-1.2 2.3C5.2 10.8 1.2 6.8 0.2 1.6z"/></svg>555 210 4789</li>
      <li><svg viewBox="0 0 12 12"><path d="M0.5 2.5h11v7h-11z M1 3l5 4 5-4" fill="none" stroke="#2e2e2e" stroke-width="1.2"/><path d="M0.5 2.5h11L6 6.6z"/></svg>info@northvale.com</li>
      <li><svg viewBox="0 0 12 12"><circle cx="6" cy="6" r="5.5"/><path d="M3 3.5c1.5 0 2 1 1.5 2s1 1.5 1 2.5M7.5 1.5c-0.5 1 0.5 2 1.5 2s1.5 1.5 1 2.5" fill="none" stroke="#f3f3f3" stroke-width="1"/></svg>www.northvale.com</li>
    </ul>
    <address class="address">northvale<br>1420 Birchwood Lane<br>Juneau, Alaska 99801</address>
  </section>

  <section class="card card--back">
    <div class="wordmark">northvale</div>
    <div class="web-band"><span>www.northvale.com</span></div>
  </section>
</body>
</html>
```